Existing Website Requiring new Pages

I have an existing word press website that was built using elementor.
Website: www.tallowcrestcare.com.au
I require the Vacancies page (https://www.tallowcrestcare.com.au/vacancies/) to be modified to display our new properties along with minor tweaks to how the information is presented.
The vacancies to be displayed are the exactly the same as those that are located on the homepage of QMR website (https://qmr.org.au/)
The new pages that link off the Vacancies tab will require custom design.
There are roughly 8 pages/properties to be incorporated. i wish for the design to be very similar to that displayed in the following link; https://www.polunda.com.au/vacancies/merrylands
Along with this the back end has not been updated for the last 3 years so it also requires some maintenance.
Website is in the disability industry and the custom pages will display information relative to Property Vacancies.
I have attached a ZIP file with some design guides, the information for each of the properties (which will need to be modified to show our business name Tallowcrest Care) and the example of how it is to look based off the Polunda website.
If you guys have any suggestions or ideas on how to make this more presentable or possible i'm open to your ideas.
Target Market(s)
People looking for SDA properties custom built for people with a disability
Industry/Entity Type
Disability
Coding
Coded - Design and coding required
Number of Pages Required
5+ page

```html
<!DOCTYPE html>
<html lang="en">
<head>
<meta charset="utf-8">
<title>Vacancies – Tallowcrest Care</title>
<link rel="stylesheet" href="https://fonts.googleapis.com/css2?family=Oswald:wght@400;500&family=Lato:wght@400;700&family=Montserrat:wght@400;600;700&display=swap">
<style>
:root{
  --white:#ffffff;
  --ink:#1f1f1f;
  --muted:#555555;
  --soft:#8a8a8a;
  --line:#d6d6d6;
  --accent:#e8795a;
  --teal:#33b9c8;
  --blue:#2a8fd0;
  --navy:#1c3f7a;
  --footer:#ffffff;
  --bar:#111111;
}
*{margin:0;padding:0;box-sizing:border-box}
html,body{width:1200px;height:4501px;overflow:hidden;background:var(--white);font-family:'Lato',sans-serif;color:var(--ink)}
.page{position:relative;width:1200px;height:4501px}

/* header */
.site-header{position:absolute;top:0;left:0;width:1200px;height:138px;background:var(--white)}
.brand{position:absolute;left:100px;top:38px;display:flex;align-items:center;gap:10px}
.brand-dot{width:34px;height:34px;border-radius:50%;background:var(--teal)}
.brand-name{font-family:'Oswald',sans-serif;font-weight:400;font-size:26px;color:var(--navy);line-height:1.05;width:110px}
.main-nav{position:absolute;left:512px;top:64px;display:flex;gap:25px;font-family:'Montserrat',sans-serif;font-weight:700;font-size:11.5px;letter-spacing:.6px}
.main-nav a{color:#333;text-decoration:none}
.main-nav a.active{color:var(--accent)}
.main-nav a.active::after{content:" ▾";font-size:9px}

/* hero */
.hero{position:absolute;top:138px;left:0;width:1200px;height:411px;
  background:linear-gradient(180deg,#3a2a1f 0%,#a86a36 28%,#f0b45a 45%,#c98a4a 62%,#d9954e 78%,#b4703a 100%)}
.hero-title{position:absolute;left:112px;top:150px;font-family:'Oswald',sans-serif;font-weight:500;font-size:76px;letter-spacing:1px;color:var(--white)}

/* cards */
.vacancies{position:absolute;top:631px;left:112px;width:976px}
.listing{position:absolute;left:0;width:976px;height:374px;border:1px solid var(--line);background:var(--white)}
.listing-photo{position:absolute;top:36px;width:452px;height:302px}
.listing.photo-left .listing-photo{left:36px}
.listing.photo-right .listing-photo{left:487px}
.listing-body{position:absolute;top:92px;width:400px}
.listing.photo-left .listing-body{left:559px}
.listing.photo-right .listing-body{left:54px}
.listing-title{font-family:'Oswald',sans-serif;font-weight:500;font-size:31px;letter-spacing:.5px;text-transform:uppercase;color:var(--ink);line-height:1.2}
.listing-type{margin-top:14px;font-size:19px;color:var(--muted)}
.listing-text{margin-top:12px;font-size:13.5px;line-height:30px;color:#222}

/* footer */
.site-footer{position:absolute;top:4140px;left:0;width:1200px;height:284px;background:var(--footer);box-shadow:0 -10px 18px rgba(0,0,0,.04)}
.footer-brand{position:absolute;left:110px;top:60px;display:flex;align-items:center;gap:10px}
.footer-brand .brand-dot{width:40px;height:40px}
.footer-brand .brand-name{font-size:30px;width:130px}
.contact-list{position:absolute;left:110px;top:205px;list-style:none;font-size:12.5px;color:var(--soft);line-height:23px}
.contact-list li{display:flex;align-items:center;gap:8px}
.contact-list svg{width:13px;height:13px}
.social{position:absolute;left:545px;top:50px;list-style:none;display:flex;flex-direction:column;gap:11px}
.social li{width:32px;height:32px;border-radius:50%;background:var(--navy)}
.social li.listing-badge{background:#6b2c8f}
.footer-col{position:absolute;top:48px;width:240px}
.footer-col.accommodation{left:643px}
.footer-col.services{left:907px}
.footer-col h3{font-family:'Montserrat',sans-serif;font-weight:600;font-size:13px;letter-spacing:.6px;color:#333;border-left:3px solid var(--blue);padding-left:12px;line-height:16px;margin-bottom:12px;text-transform:uppercase}
.footer-col ul{list-style:none;border-top:1px solid #ececec}
.footer-col li{font-family:'Montserrat',sans-serif;font-size:12.5px;color:var(--soft);line-height:22px;padding:6px 0 5px;border-bottom:1px solid #ececec}
.copyright{position:absolute;top:4424px;left:0;width:1200px;height:77px;background:var(--bar);color:var(--white);font-size:14px;font-weight:700;display:flex;align-items:center;justify-content:center}
</style>
</head>
<body>
<div class="page">

<header class="site-header">
  <div class="brand"><span class="brand-dot"></span><span class="brand-name">Tallowcrest Care</span></div>
  <nav class="main-nav">
    <a href="#">HOME</a><a href="#">ABOUT US</a><a href="#" class="active">WHAT WE DO</a><a href="#">REFERRALS</a><a href="#">FEEDBACK</a><a href="#">CONTACT US</a>
  </nav>
</header>

<section class="hero" role="img" aria-label="Person in a wheelchair raising arms on a beach at sunset">
  <h1 class="hero-title">VACANCIES</h1>
</section>

<main class="vacancies">
  <article class="listing photo-left" style="top:0">
    <div class="listing-photo" role="img" aria-label="Single storey brick home with garage and hedges" style="background:linear-gradient(180deg,#dfe6ef 0%,#c6cbd0 45%,#8a7e70 65%,#5e8a48 100%)"></div>
    <div class="listing-body"><h2 class="listing-title">Penrith</h2><p class="listing-type">4 Bedroom SIL Home</p><p class="listing-text">Lorem ipsum dolor sit amet, consectetur adipiscing elit, sed ncididunt ut labore et dolore magna aliqua</p></div>
  </article>

  <article class="listing photo-right" style="top:436px">
    <div class="listing-photo" role="img" aria-label="Red brick home with hedges and paved driveway" style="background:linear-gradient(180deg,#a9cde8 0%,#c2a58a 35%,#9a5b40 55%,#4f8a3a 75%,#b59a7e 100%)"></div>
    <div class="listing-body"><h2 class="listing-title">Mount Druitt</h2><p class="listing-type">4 Bedroom SIL Home</p><p class="listing-text">Lorem ipsum dolor sit amet, consectetur adipiscing elit, sed ncididunt ut labore et dolore magna aliqua</p></div>
  </article>

  <article class="listing photo-left" style="top:880px">
    <div class="listing-photo" role="img" aria-label="Cream rendered home with dark roof under blue sky" style="background:linear-gradient(180deg,#5fb6ef 0%,#8cc9f0 30%,#e6d9b8 55%,#3f6b34 80%,#b7b2a6 100%)"></div>
    <div class="listing-body"><h2 class="listing-title">Casula</h2><p class="listing-type">4 Bedroom SIL Home</p><p class="listing-text">Lorem ipsum dolor sit amet, consectetur adipiscing elit, sed ncididunt ut labore et dolore magna aliqua</p></div>
  </article>

  <article class="listing photo-right" style="top:1313px">
    <div class="listing-photo" role="img" aria-label="Two storey grey weatherboard home with lawn" style="background:linear-gradient(180deg,#cfe0ef 0%,#8a96a4 35%,#6e7884 60%,#4f8a3a 85%,#3d6e2d 100%)"></div>
    <div class="listing-body"><h2 class="listing-title">Mount Druitt</h2><p class="listing-type">4 Bedroom SIL Home</p><p class="listing-text">Lorem ipsum dolor sit amet, consectetur adipiscing elit, sed ncididunt ut labore et dolore magna aliqua</p></div>
  </article>

  <article class="listing photo-left" style="top:1748px">
    <div class="listing-photo" role="img" aria-label="White two storey home with lit verandah at dusk" style="background:linear-gradient(180deg,#3b5f9e 0%,#6b84b8 35%,#b9b3a8 60%,#d9a45a 78%,#2e3a2a 100%)"></div>
    <div class="listing-body"><h2 class="listing-title">Penrith</h2><p class="listing-type">4 Bedroom SIL Home</p><p class="listing-text">Lorem ipsum dolor sit amet, consectetur adipiscing elit, sed ncididunt ut labore et dolore magna aliqua</p></div>
  </article>

  <article class="listing photo-right" style="top:2182px">
    <div class="listing-photo" role="img" aria-label="Cream federation style home with blue shutters" style="background:linear-gradient(180deg,#b9d8ef 0%,#e5d3b8 35%,#d9c3a2 65%,#c9b590 100%)"></div>
    <div class="listing-body"><h2 class="listing-title">Eastwood</h2><p class="listing-type">4 Bedroom SIL Home</p><p class="listing-text">Lorem ipsum dolor sit amet, consectetur adipiscing elit, sed ncididunt ut labore et dolore magna aliqua</p></div>
  </article>

  <article class="listing photo-left" style="top:2626px">
    <div class="listing-photo" role="img" aria-label="Brick home with double garage and palm tree" style="background:linear-gradient(180deg,#8ec6ef 0%,#b9dcf2 35%,#b08a6a 55%,#4f9a3a 78%,#c9a98a 100%)"></div>
    <div class="listing-body"><h2 class="listing-title">Baulkham Hills</h2><p class="listing-type">4 Bedroom SIL Home</p><p class="listing-text">Lorem ipsum dolor sit amet, consectetur adipiscing elit, sed ncididunt ut labore et dolore magna aliqua</p></div>
  </article>

  <article class="listing photo-right" style="top:3060px">
    <div class="listing-photo" role="img" aria-label="Orange brick home with long concrete driveway" style="background:linear-gradient(180deg,#5aa7e6 0%,#a9d0f0 35%,#c96a3a 55%,#5a9a3a 72%,#c7c3bb 100%)"></div>
    <div class="listing-body"><h2 class="listing-title">Merrylands</h2><p class="listing-type">4 Bedroom SIL Home</p><p class="listing-text">Lorem ipsum dolor sit amet, consectetur adipiscing elit, sed ncididunt ut labore et dolore magna aliqua</p></div>
  </article>
</main>

<footer class="site-footer">
  <div class="footer-brand"><span class="brand-dot"></span><span class="brand-name">Tallowcrest Care</span></div>
  <ul class="contact-list">
    <li><svg viewBox="0 0 14 14"><rect x="1" y="3" width="12" height="8" fill="none" stroke="#e0457a" stroke-width="1.4"/><path d="M1 3l6 5 6-5" fill="none" stroke="#e0457a" stroke-width="1.4"/></svg>Email: info@tallowcrestcare.com.au</li>
    <li><svg viewBox="0 0 14 14"><path d="M3 1l3 3-1.5 1.5a8 8 0 0 0 4 4L10 8l3 3-2 2C6 13 1 8 1 3z" fill="#e0457a"/></svg>Phone: +61 0455 318 642</li>
    <li><svg viewBox="0 0 14 14"><circle cx="7" cy="7" r="5.5" fill="none" stroke="#e0457a" stroke-width="1.4"/><path d="M7 4v3.5l2 1.5" fill="none" stroke="#e0457a" stroke-width="1.4"/></svg>Operating Hours: 9AM To 5PM Monday - Friday</li>
  </ul>
  <ul class="social" aria-label="Social links">
    <li class="listing-badge"></li><li></li><li></li><li></li>
  </ul>
  <div class="footer-col accommodation">
    <h3>Accommodation</h3>
    <ul>
      <li>Supported Independent Living (SIL)</li>
      <li>Specialist Disability Accommodation (SDA)</li>
      <li>Short term Accommodation (Respite)</li>
      <li>Vacancies</li>
    </ul>
  </div>
  <div class="footer-col services">
    <h3>What We Do</h3>
    <ul>
      <li>In Home Care</li>
      <li>Social &amp; Community Services</li>
      <li>Therapeutic Supports</li>
      <li>Support Coordination</li>
      <li>Home Modifications</li>
    </ul>
  </div>
</footer>

<div class="copyright">Copyrights@2024.TallowcrestCare.all Rights Reserved</div>
</div>
</body>
</html>
```